Business Card Design needed for start up company Halvora

In need of a new business card designed for a start up company based in Sydney, Halvora is a new start up innovative Company, our mission it to make property accessible for everyday Australian and to become the leading Real Estate platform in Australia. We want it to be fresh and clean.

Industry/Entity Type

Financial

Contact Information for Business Card

Section for Name
Section for Title

HALVORA - The Strength of Pooling
Mobile:
Direct:

Font styles to use
Sans Serif

Colors
33a6d7
0692cd
0255a3
ffffff

Requirements
Must have
• Logo, all business card details

```html
<!DOCTYPE html>
<html lang="en">
<head>
<meta charset="UTF-8">
<title>Halvora Business Card</title>
<link href="https://fonts.googleapis.com/css2?family=Open+Sans:wght@400;600;700&display=swap" rel="stylesheet">
<style>
  :root {
    --stage: #000000;
    --sky: #2a9dd9;
    --navy: #213f78;
    --brand-blue: #2a9bd6;
    --brand-navy: #1f3f7a;
    --white: #ffffff;
    --divider: rgba(255,255,255,0.35);
  }
  * { margin: 0; padding: 0; box-sizing: border-box; }
  html, body {
    width: 1200px; height: 900px; overflow: hidden;
    background: var(--stage);
    font-family: "Open Sans", Arial, sans-serif;
  }
  .card {
    position: absolute;
    top: 271px;
    width: 457px; height: 281px;
    border-radius: 13px;
  }
  .card-front {
    left: 137px;
    background: linear-gradient(180deg, var(--sky) 0%, #2570b0 55%, var(--navy) 100%);
    color: var(--white);
  }
  .card-back {
    left: 626px;
    background: var(--white);
    display: flex; align-items: center; justify-content: center;
  }
  .wordmark { display: flex; align-items: center; }
  .wordmark-dot { border-radius: 50%; flex-shrink: 0; }
  .wordmark-name { font-weight: 700; letter-spacing: -0.5px; line-height: 1; white-space: nowrap; }

  .front-mark { position: absolute; left: 44px; top: 113px; }
  .front-mark .wordmark-dot { width: 46px; height: 46px; background: var(--white); margin-right: 7px; }
  .front-mark .wordmark-name { font-size: 24px; color: var(--white); }

  .divider {
    position: absolute; left: 232px; top: 70px;
    width: 1px; height: 142px; background: var(--divider);
  }
  .person { position: absolute; left: 257px; top: 80px; }
  .person-name { font-size: 16px; font-weight: 600; line-height: 22px; }
  .person-title { font-size: 12px; line-height: 16px; }

  .contacts { position: absolute; left: 257px; top: 140px; list-style: none; }
  .contacts li {
    display: flex; align-items: center;
    font-size: 12px; line-height: 18.5px;
  }
  .contacts svg { width: 10px; height: 10px; margin-right: 8px; fill: var(--white); }

  .tagline {
    position: absolute; left: 0; right: 0; top: 219px;
    text-align: center; font-size: 18px; font-weight: 600;
  }

  .back-mark .wordmark-dot { width: 88px; height: 88px; background: var(--brand-blue); margin-right: 10px; }
  .back-mark .wordmark-name { font-size: 41px; color: var(--brand-navy); }
</style>
</head>
<body>
  <section class="card card-front">
    <div class="wordmark front-mark">
      <span class="wordmark-dot"></span>
      <span class="wordmark-name">HALVORA</span>
    </div>
    <div class="divider"></div>
    <div class="person">
      <p class="person-name">Daniel Marsh</p>
      <p class="person-title">Managing Director</p>
    </div>
    <ul class="contacts">
      <li>
        <svg viewBox="0 0 10 10" aria-hidden="true"><path d="M2 0.5 L3.6 2.6 L2.8 3.6 Q3.8 5.8 6.4 7.2 L7.4 6.4 L9.5 8 L8.4 9.5 Q4.5 9.4 1.6 6.2 Q0.4 4.2 0.6 1.6 Z"/></svg>
        (02)-8031-5524
      </li>
      <li>
        <svg viewBox="0 0 10 10" aria-hidden="true"><path d="M2.5 0 H7.5 Q8.2 0 8.2 0.8 V9.2 Q8.2 10 7.5 10 H2.5 Q1.8 10 1.8 9.2 V0.8 Q1.8 0 2.5 0 Z M3 1.2 V7.6 H7 V1.2 Z"/></svg>
        0412-667-309
      </li>
      <li>
        <svg viewBox="0 0 10 10" aria-hidden="true"><path d="M0.5 2 H9.5 V8 H0.5 Z M1.2 2.6 L5 5.4 L8.8 2.6 Z" fill-rule="evenodd"/></svg>
        daniel@halvora.au
      </li>
    </ul>
    <p class="tagline">The Strength of Pooling</p>
  </section>

  <section class="card card-back">
    <div class="wordmark back-mark">
      <span class="wordmark-dot"></span>
      <span class="wordmark-name">HALVORA</span>
    </div>
  </section>
</body>
</html>
```